Business card design needed

A laid back coffee shop that has a great feel, that becomes a bar and grill at night. We are also wanting to cater for functions etc.
The business itself is painted dark blue/charcoal and has red doors.
Would like a logo that will be recognised when seen.

Industry/Entity Type

Coffee Shop

Contact Information for Business Card

The Lantern Coffee Bar & Grill
14b Wattle St
Merrindale NSW 2291
Ph. 02 4817 6230

Logo Text

Logo styles of interest
Emblem Logo
Abstract Logo
Wordmark Logo
Requirements
Must have
• A loyalty card on the back with 2 rows of 7 stamp spaces and a place to write a name and phone number (for a draw)

```html
<!DOCTYPE html>
<html lang="en">
<head>
<meta charset="utf-8">
<title>The Lantern Coffee Bar &amp; Grill – Business Card</title>
<link rel="stylesheet" href="https://fonts.googleapis.com/css2?family=Poiret+One&display=swap">
<style>
  :root {
    --page: #ffffff;
    --card: #ffffff;
    --ink: #111111;
    --brand-red: #e8141a;
    --wash-light: #ffffff;
    --wash-warm: #f6ead8;
    --shadow: rgba(40, 45, 50, 0.55);
  }
  html, body {
    margin: 0;
    width: 1200px;
    height: 1000px;
    overflow: hidden;
    background: var(--page);
  }
  body {
    position: relative;
    font-family: "Poiret One", sans-serif;
    color: var(--ink);
  }
  .card {
    position: absolute;
    background: var(--card);
    overflow: hidden;
    box-shadow: 6px 8px 10px var(--shadow);
  }
  .card--front { left: 279px; top: 93px; width: 608px; height: 374px; }
  .card--back  { left: 278px; top: 515px; width: 612px; height: 377px; }

  .backdrop {
    position: absolute;
    inset: 0;
    background: linear-gradient(100deg, var(--wash-light) 35%, var(--wash-warm) 100%);
  }

  .layer { position: absolute; }

  /* Front */
  .brand-mark {
    left: 150px; top: 55px; width: 110px; height: 110px;
    border: 3px solid var(--brand-red);
    border-radius: 50%;
    box-sizing: border-box;
  }
  .wordmark {
    left: 0; top: 243px; width: 410px;
    text-align: center;
    font-size: 33px;
    letter-spacing: 16px;
    text-indent: 16px;
    text-transform: uppercase;
    white-space: nowrap;
  }
  .tagline {
    left: 0; top: 284px; width: 410px;
    text-align: center;
    font-size: 19px;
    letter-spacing: 0.8px;
    white-space: nowrap;
  }
  .divider {
    left: 390px; top: 90px; width: 2px; height: 195px;
    background: var(--ink);
  }
  .address {
    left: 392px; top: 123px; width: 210px;
    text-align: center;
    font-size: 23px;
    line-height: 33px;
    letter-spacing: 1.5px;
    margin: 0;
    font-style: normal;
    white-space: nowrap;
  }

  /* Back */
  .stamps {
    left: 28px; top: 36px;
    display: grid;
    grid-template-columns: repeat(7, 62px);
    grid-auto-rows: 62px;
    column-gap: 18.5px;
    row-gap: 14px;
  }
  .stamp {
    border: 3px solid var(--ink);
    border-radius: 50%;
    box-sizing: border-box;
  }
  .entry {
    left: 28px; width: 460px;
    display: flex; align-items: flex-end;
    font-size: 19px;
  }
  .entry--name  { top: 208px; }
  .entry--phone { top: 254px; }
  .entry__label { width: 97px; }
  .entry__line {
    flex: 1;
    border-bottom: 1.5px dashed var(--ink);
    margin-bottom: 5px;
  }
  .back-name {
    left: 40px; top: 313px; width: 470px;
    text-align: center;
    font-size: 22px;
    letter-spacing: 1.2px;
    white-space: nowrap;
  }
  .back-mark {
    left: 530px; top: 250px; width: 40px; height: 40px;
    border: 3px solid var(--brand-red);
    border-radius: 50%;
    box-sizing: border-box;
  }
</style>
</head>
<body>
  <section class="card card--front" aria-label="Business card front">
    <div class="backdrop" role="img" aria-label="Soft warm background texture area"></div>
    <div class="layer brand-mark" aria-hidden="true"></div>
    <div class="layer wordmark">The Lantern</div>
    <div class="layer tagline">Coffee Bar &amp; Grill</div>
    <div class="layer divider"></div>
    <address class="layer address">
      14b Wattle St<br>
      Merrindale<br>
      NSW 2291<br>
      Ph. 02 4817 6230
    </address>
  </section>

  <section class="card card--back" aria-label="Loyalty card back">
    <div class="backdrop" role="img" aria-label="Soft warm background texture area"></div>
    <div class="layer stamps" aria-label="Loyalty stamp spaces">
      <span class="stamp"></span><span class="stamp"></span><span class="stamp"></span><span class="stamp"></span><span class="stamp"></span><span class="stamp"></span><span class="stamp"></span>
      <span class="stamp"></span><span class="stamp"></span><span class="stamp"></span><span class="stamp"></span><span class="stamp"></span><span class="stamp"></span><span class="stamp"></span>
    </div>
    <div class="layer entry entry--name"><span class="entry__label">Name</span><span class="entry__line"></span></div>
    <div class="layer entry entry--phone"><span class="entry__label">Phone</span><span class="entry__line"></span></div>
    <div class="layer back-name">THE LANTERN Coffee Bar &amp; Grill</div>
    <div class="layer back-mark" aria-hidden="true"></div>
  </section>
</body>
</html>
```